Build a landing page to promote a service (dialler consultation and support).

We are a call centre consultation firm and we need a landing page to promote a service. The service is Tormalux dialler consultation and support.
If you do not know what Tormalux is, please do some quick "Zorvex" research for more information.
The landing page will be promoted with a paid advertisement, so we want something that is simple, and explains exactly what service we offer.
There are two objectives for the landing page:
1) A "call to action" which directs the user to a contact page, including a form plus all of our contact details.
2) A form for them viewers to enter their details to get a "FREE" quote for their project. This form should be placed on the main page.
Notes:
The call to action will require the viewer to enter their name, email, phone number as well as a description of their request. There will also need to be a drop down menu for the type of quote. This menu should have the following options:
1) Tormalux support
2) Tormalux hosting
3) Tormalux customisation
4) Other
We need 2 pages in total:
1) Main landing page
This is the home page. It will need to clearly indicate our services and our key selling features.
Services:
* Tormalux support
* Tormalux hosting
* Tormalux customisation
Key Selling Features:
* Australian based
* PCI complaint
* 10+ years of dialler and call centre experience
* we run a sister company which is a highly reputable 40 seat call centre, so we know first hand about call centre technology.
The main landing page will have an "about us" section with a few paragraphs about how we got started.
-------------------------------------------------------------------------
2) Contact page
All of our contact details will live on this page, as well as a contact form.
Other notes:
We will be self hosting the landing page.
We already have a domain name.
The design must be clean and incorporate our logo, as well as it's colours. (Logo attached)
We want a fully function HTML landing page, not just a "PSD" design.
The page must be mobile optimised.
Anyone using Tormalux software.

```html
<!DOCTYPE html>
<html lang="en">
<head>
<meta charset="utf-8">
<title>Halvora – Tormalux support and call centre technology</title>
<link rel="stylesheet" href="https://fonts.googleapis.com/css2?family=Lato:wght@400;700&family=PT+Sans:wght@700&display=swap">
<style>
  :root {
    --brand-ink: #4a90c8;
    --nav-ink: #2b2b2b;
    --accent: #d96d52;
    --accent-bright: #e66a4d;
    --hero-top: #6f93bb;
    --hero-mid: #5a80ab;
    --hero-bottom: #3e6591;
    --white: #ffffff;
  }
  * { box-sizing: border-box; margin: 0; padding: 0; }
  html, body { width: 1200px; height: 630px; overflow: hidden; }
  body { font-family: "Lato", Arial, sans-serif; background: var(--white); position: relative; }

  .site-header {
    position: absolute; top: 0; left: 0; width: 1200px; height: 47px;
    background: var(--white);
  }
  .brand {
    position: absolute; left: 150px; top: 10px;
    font-size: 21px; line-height: 26px; font-weight: 700; color: var(--brand-ink);
    letter-spacing: 0.5px; text-decoration: none;
  }

  .main-nav a {
    position: absolute; top: 15px; font-size: 12.5px; letter-spacing: 1px; color: var(--nav-ink);
    text-decoration: none; text-transform: uppercase; white-space: nowrap;
  }
  .nav-services { left: 465px; }
  .nav-about { left: 550px; }
  .nav-why { left: 642px; }
  .nav-contact { left: 780px; }
  .nav-quote {
    position: absolute; left: 882px; top: 6px; width: 165px; height: 32px; border-radius: 16px;
    background: var(--accent); color: var(--white); font-size: 12.5px; font-weight: 700;
    letter-spacing: 0.8px; display: flex; align-items: center; justify-content: center; text-decoration: none;
  }

  .hero { position: absolute; top: 47px; left: 0; width: 1200px; height: 583px; }
  .hero-photo {
    position: absolute; inset: 0;
    background: linear-gradient(160deg, var(--hero-top) 0%, var(--hero-mid) 45%, var(--hero-bottom) 100%);
  }
  .hero-content { position: absolute; left: 165px; top: 98px; color: var(--white); }
  .hero-title {
    font-family: "PT Sans", Arial, sans-serif; font-weight: 700; font-size: 46px; line-height: 54px;
    white-space: nowrap;
  }
  .hero-lead { margin-top: 26px; font-size: 16.5px; line-height: 25px; white-space: nowrap; }
  .hero-cta {
    display: flex; align-items: center; justify-content: center; margin-top: 41px;
    width: 205px; height: 42px; border-radius: 21px; background: var(--accent-bright);
    color: var(--white); font-weight: 700; font-size: 14px; letter-spacing: 0.6px; text-decoration: none;
  }
</style>
</head>
<body>
  <header class="site-header">
    <a class="brand" href="#">Halvora</a>
    <nav class="main-nav">
      <a class="nav-services" href="#">Services</a>
      <a class="nav-about" href="#">About us</a>
      <a class="nav-why" href="#">Why Halvora</a>
      <a class="nav-contact" href="#">Contact us</a>
    </nav>
    <a class="nav-quote" href="#">GET A QUOTE</a>
  </header>

  <section class="hero">
    <div class="hero-photo" role="img" aria-label="Call centre agents wearing headsets working at computer desks, under a blue tint"></div>
    <div class="hero-content">
      <h1 class="hero-title">A holistic approach to<br>Tormalux support and<br>call centre technology</h1>
      <p class="hero-lead">A complete Tormalux call center consultation for better service,<br>productivity and profitability.</p>
      <a class="hero-cta" href="#">GET A FREE QUOTE</a>
    </div>
  </section>
</body>
</html>
```